Business card design for new eCommerce site focusing on integrity and strong businsess tactics

We need a business card that will stand out and be memorable. Something with color that matches our company logo colors. Think high end version of Pactivo. There are 2 logos provided. The parent company is called Amber Ledge Partners and we are presenting a new and very exciting eCommerce site called BrightHarborTrade.example.

Target Market(s)

Our target markets are in the Activities, Food and Beverage, Health and Beauty

Industry/Entity Type

Marketing

Contact Information for Business Card

We have 4 members that need cards...I will provide all info to the winner of the design contest
Business Address is
4870 West 63rd Avenue, Suite C207
Phoenix AZ 85731

Font styles to use
Serif
Sans Serif

Colors

Designer to choose colors to be used in the design.

Requirements
Must have
• The card must be memorable...should be unique in design but must exude integrity and be playful .
• I have provided several colors or our parent company...please feel free to use which ever
Nice to have
• I will leave this up to you. Feel free to use other images of your choosing that wraps around our client.....Activities, Dining, Health, Beauty
Should not have
• just dont be boring

```html
<!DOCTYPE html>
<html lang="en">
<head>
<meta charset="utf-8">
<title>BrightHarborTrade.example — Business Card</title>
<link rel="stylesheet" href="https://fonts.googleapis.com/css2?family=Open+Sans:wght@400;600;700&family=Oswald:wght@400&display=swap">
<style>
  :root {
    --backdrop: #8a6446;
    --card-white: #fbfbfa;
    --brand-blue: #2a7db4;
    --brand-green: #7dc242;
    --ink: #4a4a4a;
    --rule: #6f6f6f;
    --white: #ffffff;
  }
  * { margin: 0; padding: 0; box-sizing: border-box; }
  html, body { width: 1200px; height: 960px; overflow: hidden; }
  body {
    position: relative;
    background: var(--backdrop);
    font-family: "Open Sans", Arial, sans-serif;
  }
  .card {
    position: absolute;
    width: 600px;
    height: 345px;
    border-radius: 20px;
    overflow: hidden;
    box-shadow: 0 4px 10px rgba(0,0,0,0.35);
  }
  .card-front { left: 303px; top: 130px; background: var(--card-white); }
  .card-back { left: 298px; top: 488px; background: var(--brand-blue); }

  .brand-lockup {
    position: absolute;
    right: 34px;
    top: 66px;
    text-align: right;
  }
  .brand-name {
    display: flex;
    align-items: center;
    justify-content: flex-end;
    gap: 10px;
    font-weight: 600;
    font-size: 21px;
    color: var(--brand-green);
    line-height: 1;
  }
  .brand-dot {
    width: 16px; height: 16px; border-radius: 50%;
    background: var(--brand-blue);
  }
  .brand-tagline {
    margin-top: 6px;
    font-size: 11px;
    letter-spacing: 1px;
    color: var(--brand-blue);
  }

  .holder { position: absolute; left: 26px; top: 180px; }
  .holder-name {
    font-family: "Oswald", "Arial Narrow", sans-serif;
    font-size: 24px;
    color: var(--brand-blue);
    line-height: 1;
  }
  .holder-title {
    margin-top: 5px;
    font-size: 14px;
    color: var(--brand-green);
    line-height: 1;
  }
  .divider {
    position: absolute;
    left: 26px; right: 34px; top: 232px;
    height: 1px;
    background: var(--rule);
  }
  .contacts {
    position: absolute;
    left: 26px; top: 244px;
    list-style: none;
    font-size: 14px;
    color: var(--ink);
  }
  .contacts li {
    display: flex; align-items: center; gap: 8px;
    height: 19px;
  }
  .contacts svg { width: 13px; height: 13px; fill: var(--brand-blue); }
  .address {
    position: absolute;
    right: 32px; top: 261px;
    text-align: right;
    font-size: 14px;
    line-height: 19px;
    color: var(--ink);
  }
  .footer-band { position: absolute; left: 0; bottom: 0; width: 600px; height: 28px; }
  .site-url {
    position: absolute;
    right: 22px; bottom: 6px;
    font-size: 13px;
    line-height: 16px;
    letter-spacing: 0.4px;
    color: var(--white);
    white-space: nowrap;
  }

  .back-lockup {
    position: absolute;
    left: 0; right: 0; top: 78px;
    display: flex; flex-direction: column; align-items: center; gap: 72px;
  }
  .back-dot {
    width: 72px; height: 72px; border-radius: 50%;
    border: 6px solid var(--white);
  }
  .back-name {
    font-weight: 700;
    font-size: 34px;
    color: var(--white);
    line-height: 1;
  }
</style>
</head>
<body>

<section class="card card-front" aria-label="Business card front">
  <div class="brand-lockup">
    <div class="brand-name"><span class="brand-dot"></span>BrightHarborTrade.example</div>
    <div class="brand-tagline">Activities-Dining-Health-Beauty</div>
  </div>

  <div class="holder">
    <div class="holder-name">DANA WHITFIELD</div>
    <div class="holder-title">CEO/FOUNDER</div>
  </div>
  <div class="divider"></div>

  <ul class="contacts">
    <li>
      <svg viewBox="0 0 24 24" aria-hidden="true"><path d="M6.6 10.8a15.1 15.1 0 0 0 6.6 6.6l2.2-2.2a1 1 0 0 1 1-.25 11.4 11.4 0 0 0 3.6.57 1 1 0 0 1 1 1V20a1 1 0 0 1-1 1A17 17 0 0 1 3 4a1 1 0 0 1 1-1h3.5a1 1 0 0 1 1 1c0 1.250.2 2.450.57 3.6a1 1 0 0 1-.25 1z"/></svg>
      555 214 0387
    </li>
    <li>
      <svg viewBox="0 0 24 24" aria-hidden="true"><path d="M7 1h10a2 2 0 0 1 2 2v18a2 2 0 0 1-2 2H7a2 2 0 0 1-2-2V3a2 2 0 0 1 2-2zm0 3v14h10V4z"/></svg>
      555 730 6192
    </li>
    <li>
      <svg viewBox="0 0 24 24" aria-hidden="true"><path d="M2 5h20v14H2zm2 2v.5l8 5 8-5V7l-8 5z"/></svg>
      dana@brightharbortrade.example
    </li>
  </ul>

  <div class="address">
    4870 West 63rd Avenue<br>
    Suite C207, Phoenix AZ 85731
  </div>

  <svg class="footer-band" viewBox="0 0 600 28" aria-hidden="true">
    <path d="M0 8 H292 Q288 14 280 16 H0 Z" fill="var(--brand-green)"/>
    <path d="M312 0 H600 V28 H282 Q302 24 304 10 Q306 0 312 0 Z" fill="var(--brand-blue)"/>
  </svg>
  <div class="site-url">WWW.BRIGHTHARBORTRADE.EXAMPLE</div>
</section>

<section class="card card-back" aria-label="Business card back">
  <div class="back-lockup">
    <span class="back-dot"></span>
    <div class="back-name">Amber Ledge Partners</div>
  </div>
</section>

</body>
</html>
```